Meridale Hair Studio Needs a new appointment business card

We need a new appointment card for our hair salon.

I Dont want bright out there colours.
I would like it to be neat, clean, easy to read. White, Black, with a hint of colour if needed.

We need
-Logo
-Phone number 47268315
-Mobile Number: 0437608251
Address: Shop 5/213 Tarwin Road, The Crossgate, Mackay 4740

BACK SIDE OF CARD
- Appointment Time & Date (White background so we are able to write on it)
(If you are unable to make your appointment please contact us ASAP 47268315)

I also would like the linkpage and Snapframe logo(Find us on Linkpage)(find us on Snapframe)

Target Market(s)

appointment card simple to read. all information for their next appoint For all our clients male and female

Industry/Entity Type

Hairdresser

Contact Information for Business Card

-Logo
-Phone number 47268315

BACK SIDE OF CARD

Font styles to use
Serif
Sans Serif
Script

Requirements
Must have
• White Back ground on backside with appointment deatils so we are able to write information (like appointment time and date)
Nice to have
• Find us on Linkpage
and
snapframe - meridale_hairstudio
Should not have
• BRIGHT COLOURS

```html
<!DOCTYPE html>
<html lang="en">
<head>
<meta charset="utf-8">
<title>Meridale Hair Studio – Appointment Card</title>
<link rel="stylesheet" href="https://fonts.googleapis.com/css2?family=Arimo&family=Montserrat:wght@400;500&display=swap">
<style>
  :root{
    --ink:#0b0c0c;
    --paper:#ffffff;
    --light:#f1f1f1;
    --mist:#d6d6d6;
    --rule:#1a1a1a;
    --frame:#8a8a8a;
  }
  *{margin:0;padding:0;box-sizing:border-box}
  html,body{width:1200px;height:622px;overflow:hidden;background:var(--paper)}
  .sheet{position:relative;width:1200px;height:622px;background:var(--paper);font-family:"Montserrat",sans-serif;color:var(--ink)}
  .band{position:absolute;left:0;width:1200px;height:14px;background:var(--ink)}
  .band--top{top:0}
  .band--bottom{bottom:0}
  .presentation-title{position:absolute;top:43px;left:0;width:1200px;text-align:center;font-family:"Arimo",sans-serif;font-size:20px;line-height:24.5px}
  .option-label{position:absolute;top:152px;left:0;width:1200px;text-align:center;font-family:"Arimo",sans-serif;font-size:18px}

  .card{position:absolute;top:234px;width:468px;height:267px;overflow:hidden}
  .card--front{left:116px;background:var(--ink);color:var(--paper)}
  .card--back{left:613px;background:var(--paper);border:1px solid var(--frame)}

  .front-motif{position:absolute;left:330px;top:0;width:138px;height:267px;background:linear-gradient(120deg,rgba(241,241,241,0) 0%,rgba(241,241,241,.18) 55%,rgba(241,241,241,.05) 100%)}
  .studio-name{position:absolute;left:30px;top:62px;color:var(--paper);font-weight:500;font-size:22px;line-height:26px;white-space:nowrap}

  .contact{position:absolute;left:32px;list-style:none;font-size:14px;line-height:18px}
  .contact li{position:absolute;left:0;display:flex;gap:8px;white-space:nowrap}
  .contact svg{flex:none;width:16px;height:16px;margin-top:1px;fill:var(--paper)}
  .contact .phone{top:128px}
  .contact .mobile{top:160px}
  .contact .address{top:190px}

  .back-motif{position:absolute;left:0;top:121px;width:135px;height:146px;background:radial-gradient(ellipse at 40% 70%,rgba(214,214,214,.55),rgba(214,214,214,0) 70%)}
  .appt-heading{position:absolute;top:27px;left:0;width:100%;text-align:center;font-size:16px;font-weight:500}
  .write-row{position:absolute;top:65px;left:31px;display:flex;align-items:flex-end;font-size:14px;font-weight:500}
  .write-line{display:inline-block;border-bottom:1px solid var(--rule);height:14px}
  .write-line--date{width:157px;margin:0 11px 0 5px}
  .write-line--time{width:158px;margin-left:3px}
  .notice{position:absolute;top:90px;left:0;width:100%;text-align:center;font-size:13.5px;line-height:18px}
  .social-heading{position:absolute;top:182px;left:0;width:100%;text-align:center;font-size:16px;font-weight:500}
  .social{position:absolute;top:205px;left:0;width:100%;list-style:none;font-size:14px;line-height:24px}
  .social li{display:flex;justify-content:center;align-items:center;gap:6px}
  .social-mark{width:16px;height:16px;background:var(--ink)}
  .social-mark--square{border-radius:3px}
  .social-mark--circle{border-radius:50%;background:none;border:2px solid var(--ink)}
</style>
</head>
<body>
<main class="sheet">
  <div class="band band--top"></div>

  <header class="presentation-title">
    <p>Meridale Hair Studio</p>
    <p>Logo Design</p>
  </header>
  <p class="option-label">Option 2</p>

  <section class="card card--front" aria-label="Front of appointment card">
    <div class="front-motif" role="img" aria-label="Large open hair scissors decoration"></div>
    <h1 class="studio-name">Meridale Hair Studio</h1>
    <ul class="contact">
      <li class="phone">
        <svg viewBox="0 0 24 24" aria-hidden="true"><path d="M3 9c0-3 4-5 9-5s9 2 9 5v2h-5V9c-1-1-7-1-8 0v2H3zM7 12h10l3 8H4z"/></svg>
        47268315
      </li>
      <li class="mobile">
        <svg viewBox="0 0 24 24" aria-hidden="true"><path d="M8 2h8a2 2 0 0 1 2 2v16a2 2 0 0 1-2 2H8a2 2 0 0 1-2-2V4a2 2 0 0 1 2-2zm0 3v13h8V5zm4 14.5a1 1 0 1 0 0 .01z"/></svg>
        0437608251
      </li>
      <li class="address">
        <svg viewBox="0 0 24 24" aria-hidden="true"><path d="M12 2a7 7 0 0 1 7 7c0 5-7 13-7 13S5 14 5 9a7 7 0 0 1 7-7zm0 4.5a2.5 2.5 0 1 0 0 5 2.5 2.5 0 0 0 0-5z"/></svg>
        <span>Shop 5/213 Tarwin Road, The<br>Crossgate, Mackay 4740</span>
      </li>
    </ul>
  </section>

  <section class="card card--back" aria-label="Back of appointment card">
    <div class="back-motif" role="img" aria-label="Faint hair scissors decoration"></div>
    <h2 class="appt-heading">Appointment Details</h2>
    <div class="write-row">
      Date<span class="write-line write-line--date"></span>
      Time<span class="write-line write-line--time"></span>
    </div>
    <p class="notice">If you are unable to make your appointment<br>please contact us ASAP 47268315</p>
    <h3 class="social-heading">Find us on Social Media</h3>
    <ul class="social">
      <li><span class="social-mark social-mark--square" aria-hidden="true"></span>meridalehairstudiocrossgate</li>
      <li><span class="social-mark social-mark--circle" aria-hidden="true"></span>meridale_hairstudio</li>
    </ul>
  </section>

  <div class="band band--bottom"></div>
</main>
</body>
</html>
```